Detail Shop Business card design

i need a business card design for my new detailing company called 'Brisk's Polish Works'. i want an all black and white design . simple, direct and to the point. i want the designer to choose a fitting font to match the logothe front should have logo, address, phone and email and the back side should have a slogan and text indicating that we offer services on anything including cars, trucks, motorcycles and RVs. slogan will read "we take pride in your ride"
maybe also very small on the back side the IG icon with Brisks_Polish_Works

phone 208.417.6352
address 3847 E Larkin Ave
Spokane WA 99214
email: BrisksPolish@mailvexo.com

Target Market(s)

all ages , auto enthusiasts

Industry/Entity Type

Automotive

Contact Information for Business Card

the front should have logo, address, phone and email and the back side should have a slogan and text indicating that we offer services on anything including cars, trucks, motorcycles and RVs. slogan will read "we take pride in your ride"

phone 208.417.6352
address 3847 E Larkin Ave
Spokane WA 99214

Colors
000000
ffffff

Requirements
Must have
• bold font and very simple design with good spacing
Nice to have
• anything creative from the designer indicating we service any types of vehicles
Should not have
• any colors ,

```html
<!DOCTYPE html>
<html lang="en">
<head>
<meta charset="utf-8">
<title>Brisk's Polish Works – Business Card</title>
<link rel="stylesheet" href="https://fonts.googleapis.com/css2?family=Roboto:wght@400;500;700;900&family=Oswald:wght@400&display=swap">
<style>
  :root {
    --ink: #111111;
    --ink-soft: #4a4a4a;
    --paper: #f4f4f4;
    --stage: #e6e6e6;
  }
  * { box-sizing: border-box; margin: 0; padding: 0; }
  html, body { width: 1200px; height: 960px; overflow: hidden; }
  body {
    background: var(--stage);
    position: relative;
    font-family: "Roboto", Arial, sans-serif;
    color: var(--ink);
  }
  .card {
    position: absolute;
    width: 600px;
    height: 342px;
    background: var(--paper);
  }
  .card--front { left: 314px; top: 113px; }
  .card--back { left: 311px; top: 472px; }

  /* Front */
  .brand {
    position: absolute;
    left: 32px; top: 22px;
    width: 200px; height: 178px;
    display: flex; flex-direction: column; align-items: center; justify-content: center;
    gap: 12px;
  }
  .brand__dot {
    width: 26px; height: 26px; border-radius: 50%;
    background: var(--ink);
  }
  .brand__name {
    font-weight: 900;
    font-size: 26px;
    line-height: 1.05;
    text-align: center;
    text-transform: uppercase;
    color: var(--ink);
  }
  .person {
    position: absolute;
    right: 38px; top: 124px;
    text-align: right;
  }
  .person__name { font-weight: 500; font-size: 21px; letter-spacing: 0.2px; line-height: 1; }
  .person__role { font-size: 14px; color: var(--ink-soft); margin-top: 6px; letter-spacing: 0.3px; }
  .rule {
    position: absolute;
    left: 356px; top: 182px;
    width: 206px; height: 6px;
    background: var(--ink);
  }
  .contact {
    position: absolute;
    right: 38px; top: 204px;
    text-align: right;
    font-size: 14px;
    color: var(--ink-soft);
    line-height: 18px;
  }
  .contact__address { margin-bottom: 3px; margin-right: 1px; }
  .contact__row { display: flex; justify-content: flex-end; align-items: center; gap: 10px; height: 19.5px; }
  .contact__icon { width: 13px; height: 13px; fill: var(--ink); flex: none; }

  /* Back */
  .vehicle-art {
    position: absolute;
    left: 114px; top: 90px;
    width: 380px; height: 136px;
    background: linear-gradient(180deg, #2a2a2a 0%, #111 70%, #3a3a3a 100%);
    border-radius: 40px 40px 6px 6px;
  }
  .slogan {
    position: absolute;
    left: 0; right: 0; top: 272px;
    text-align: center;
  }
  .slogan__title {
    display: inline-block;
    font-weight: 700;
    font-size: 17px;
    letter-spacing: 0.3px;
    padding: 0 14px 4px;
    border-bottom: 1.5px solid var(--ink);
  }
  .slogan__services {
    font-family: "Oswald", "Arial Narrow", sans-serif;
    font-size: 13.5px;
    margin-top: 3px;
    letter-spacing: 0.1px;
  }
</style>
</head>
<body>

<section class="card card--front" aria-label="Business card front">
  <div class="brand">
    <span class="brand__dot"></span>
    <span class="brand__name">Brisk's Polish Works</span>
  </div>

  <div class="person">
    <p class="person__name">MARCUS REED</p>
    <p class="person__role">CEO/FOUNDER</p>
  </div>

  <div class="rule"></div>

  <address class="contact" style="font-style: normal;">
    <p class="contact__address">3847 E Larkin Ave<br>Spokane WA 99214</p>
    <p class="contact__row">208.417.6352
      <svg class="contact__icon" viewBox="0 0 16 16" aria-hidden="true"><path d="M3.6 1l2.3 2.6-1.2 2a9.5 9.5 0 0 0 5.7 5.7l2-1.2L15 12.4l-1.5 2.3C7.5 15 1 8.5 1.3 2.5z"/></svg>
    </p>
    <p class="contact__row">836 552 7140
      <svg class="contact__icon" viewBox="0 0 16 16" aria-hidden="true"><path d="M4 0h8a1 1 0 0 1 1 1v14a1 1 0 0 1-1 1H4a1 1 0 0 1-1-1V1a1 1 0 0 1 1-1zm1 2v10h6V2zm3 11a1 1 0 1 0 0 2 1 1 0 0 0 0-2z"/></svg>
    </p>
    <p class="contact__row">BrisksPolish@mailvexo.com
      <svg class="contact__icon" viewBox="0 0 16 16" aria-hidden="true"><path d="M1 3h14v10H1zm1.2 1.2L8 8.6l5.8-4.4z" fill-rule="evenodd"/></svg>
    </p>
    <p class="contact__row">www.briskspolish.com
      <svg class="contact__icon" viewBox="0 0 16 16" aria-hidden="true"><circle cx="8" cy="8" r="7"/><path d="M4 5c2 0 2 2 4 2s1 3-1 3-1 3-3 2z" fill="#f4f4f4"/></svg>
    </p>
  </address>
</section>

<section class="card card--back" aria-label="Business card back">
  <div class="vehicle-art" role="img" aria-label="Black silhouette illustration of a hot rod car"></div>
  <div class="slogan">
    <p class="slogan__title">WE TAKE PRIDE IN YOUR RIDE</p>
    <p class="slogan__services">we offer services on anything including cars, trucks, motorcycles &amp; RVs</p>
  </div>
</section>

</body>
</html>
```